Business Card for beauty technology startup

Design Glimora Business Card for a Beauty, based on the website identity and colors (https://www.glimora-example.com).
Glimora is a beauty tech startup that gathers helpful product info for beauty lovers and consumers (such as availability on stores, price range and product reviews) for makeup products. The card design must be young, colorful but clean, and very modern.

Target Market(s)

woman, 15-35

Industry/Entity Type

Cosmetics

Contact Information for Business Card

Full Name, address, phone

Font styles to use
Other font styles liked:
• Advent Pro

Colors
e34297
86cfc6
ffffff
5c5c5c
e8e8e8
e667a6
b2b2b2

Requirements
Must have
• One full colored side with a creative design and another with card info
• Use Color palette: #95C5C5 and/or #D38AA5
• Use fonts: Advent Pro
• Use website identity: https://www.glimora-example.com
Nice to have
• If needed extra font: Roboto

```html
<!DOCTYPE html>
<html lang="en">
<head>
<meta charset="UTF-8">
<title>Glimora Business Card</title>
<link rel="stylesheet" href="https://fonts.googleapis.com/css2?family=Advent+Pro:wght@300;400;500;600&display=swap">
<style>
  :root {
    --canvas-bg: #e8e8e8;
    --card-deep: #8e3d62;
    --card-mid: #b8678a;
    --card-light: #d38aa5;
    --disc-light: #f6eef1;
    --disc-edge: #e9d3dc;
    --brand-ink: #8e2f5a;
    --accent-ring: #95c5c5;
    --text-light: #ffffff;
    --text-soft: #f4e6ec;
  }
  * { margin: 0; padding: 0; box-sizing: border-box; }
  html, body {
    width: 1200px;
    height: 969px;
    overflow: hidden;
    background: var(--canvas-bg);
    font-family: "Advent Pro", "Roboto", Arial, sans-serif;
  }
  .card {
    position: absolute;
    left: 100px;
    top: 199px;
    width: 1000px;
    height: 571px;
    overflow: hidden;
    background: linear-gradient(100deg, var(--card-deep) 0%, var(--card-mid) 50%, var(--card-light) 100%);
    box-shadow: 0 18px 40px rgba(60, 20, 40, 0.18);
  }
  .brand-disc {
    position: absolute;
    left: 432px;
    top: 34px;
    width: 554px;
    height: 554px;
    border-radius: 50%;
    background: radial-gradient(circle at 45% 40%, var(--disc-light) 0%, var(--disc-light) 58%, var(--disc-edge) 100%);
  }
  .brand-mark {
    position: absolute;
    left: 639px;
    top: 150px;
    width: 150px;
    height: 150px;
    border-radius: 50%;
    border: 4px solid var(--accent-ring);
  }
  .brand-name {
    position: absolute;
    left: 464px;
    top: 358px;
    width: 500px;
    text-align: center;
    font-size: 76px;
    font-weight: 400;
    letter-spacing: 8px;
    color: var(--brand-ink);
    line-height: 1;
  }
  .contact {
    position: absolute;
    left: 52px;
    top: 110px;
    color: var(--text-light);
  }
  .contact .person-name {
    font-size: 28px;
    font-weight: 600;
    letter-spacing: 0.5px;
    line-height: 1.2;
  }
  .contact .person-role {
    font-size: 27px;
    font-weight: 500;
    line-height: 1.2;
    color: var(--text-soft);
  }
  .contact .address {
    margin-top: 36px;
    font-size: 26px;
    font-weight: 500;
    line-height: 1.3;
    font-style: normal;
    color: var(--text-soft);
  }
  .contact .channels {
    margin-top: 16px;
    list-style: none;
  }
  .contact .channels li {
    display: flex;
    align-items: center;
    gap: 14px;
    font-size: 26px;
    font-weight: 500;
    line-height: 1.24;
    color: var(--text-soft);
  }
  .channels svg {
    width: 17px;
    height: 17px;
    fill: var(--text-soft);
    flex: none;
  }
</style>
</head>
<body>
  <section class="card" aria-label="Glimora business card">
    <div class="brand-disc"></div>
    <div class="brand-mark"></div>
    <div class="brand-name">GLIMORA</div>

    <div class="contact">
      <p class="person-name">CLARA VANCE</p>
      <p class="person-role">CEO/FOUNDER</p>
      <address class="address">214 Orchid Row<br>Lakemont, Oregon 97410</address>
      <ul class="channels">
        <li>
          <svg viewBox="0 0 16 16" aria-hidden="true"><path d="M1 5c0-2 2-3 7-3s7 1 7 3v1h-4V4.5H5V6H1z"/><path d="M3 7h10l1 7H2z"/></svg>
          555 210 4836
        </li>
        <li>
          <svg viewBox="0 0 16 16" aria-hidden="true"><path d="M4 0h8v16H4z M5.5 2v10h5V2z"/></svg>
          555 318 7702
        </li>
        <li>
          <svg viewBox="0 0 16 16" aria-hidden="true"><path d="M4 1h8v4H4z"/><path d="M1 6h14v7H1z M4 10v5h8v-5z"/></svg>
          555 402 6159
        </li>
        <li>
          <svg viewBox="0 0 16 16" aria-hidden="true"><path d="M1 3h14v1.5L8 9 1 4.5z"/><path d="M1 6.2 8 10.7l7-4.5V13H1z"/></svg>
          info@glimora-example.com
        </li>
        <li>
          <svg viewBox="0 0 16 16" aria-hidden="true"><circle cx="8" cy="8" r="7"/></svg>
          www.glimora-example.com
        </li>
      </ul>
    </div>
  </section>
</body>
</html>
```